Business Card Design for Training Business

Clear Path Coaching is a new business that delivers training and other services with a focus on topics related to mental health and wellbeing, for example, Wellmind Response Course, Resilience etc. We have a strong focus on evidence-based psychology and neuroscience. I have a logo which I will upload with the brief, so please consider colours that work well with the logo.
Target Market(s)
Adults, workplaces (particularly government and not-for-profits)
Industry/Entity Type
Business
Contact Information for Business Card
Head Strong TrainingSamantha SellwoodDirector0438 770 850sam@headstrongtraining.com.auwww.headstrongtraining.com.au

```html
<!DOCTYPE html>
<html lang="en">
<head>
<meta charset="utf-8">
<title>Clear Path Coaching – Business Card</title>
<link rel="stylesheet" href="https://fonts.googleapis.com/css2?family=Questrial&display=swap">
<style>
  :root {
    --teal: #22b8bd;
    --teal-deep: #1fb0b5;
    --ink: #555555;
    --grey: #808080;
    --paper: #f7f7f7;
    --backdrop: #3b3b3b;
    --white: #ffffff;
  }
  * { margin: 0; padding: 0; box-sizing: border-box; }
  html, body {
    width: 1200px;
    height: 750px;
    overflow: hidden;
    background: var(--backdrop);
    font-family: "Questrial", "Century Gothic", sans-serif;
  }
  .card {
    position: absolute;
    left: 371px;
    width: 461px;
    height: 262px;
    border-radius: 14px;
    overflow: hidden;
  }
  .card--front { top: 106px; background: var(--paper); }
  .card--back { top: 387px; background: var(--teal); }

  .card__curves { position: absolute; inset: 0; }

  .brand {
    position: absolute;
    left: 258px;
    top: 22px;
    width: 200px;
    text-align: center;
  }
  .brand__dot {
    display: block;
    margin: 0 auto 10px;
    width: 58px;
    height: 58px;
    border: 2px solid var(--teal);
    border-radius: 50%;
  }
  .brand__name {
    color: var(--grey);
    font-size: 16px;
    letter-spacing: 3px;
    line-height: 19px;
  }

  .person {
    position: absolute;
    left: 24px;
    top: 148px;
  }
  .person__name {
    color: var(--teal);
    font-size: 18px;
    line-height: 22px;
  }
  .person__role {
    color: var(--ink);
    font-size: 13px;
    line-height: 17px;
  }
  .contacts {
    list-style: none;
    margin-top: 12px;
  }
  .contacts__item {
    display: flex;
    align-items: center;
    gap: 6px;
    color: var(--ink);
    font-size: 12px;
    line-height: 17.5px;
  }
  .contacts__icon { width: 12px; height: 12px; flex: none; }

  .back-mark {
    position: absolute;
    left: 50%;
    top: 76px;
    width: 112px;
    height: 112px;
    margin-left: -56px;
    border: 2px solid var(--white);
    border-radius: 50%;
    display: flex;
    align-items: center;
    justify-content: center;
    text-align: center;
    color: var(--white);
    font-size: 13px;
    letter-spacing: 2px;
    line-height: 17px;
  }
  .back-url {
    position: absolute;
    left: 0;
    right: 0;
    top: 226px;
    text-align: center;
    color: var(--white);
    font-size: 12.5px;
  }
</style>
</head>
<body>

<section class="card card--front">
  <svg class="card__curves" viewBox="0 0 461 262" width="461" height="262" aria-hidden="true">
    <path d="M0 0 H104 C52 20 12 60 0 112 Z" fill="var(--teal)"/>
    <path d="M112 1 C58 21 16 62 4 124" fill="none" stroke="var(--grey)" stroke-width="3"/>
    <path d="M461 160 C440 210 400 245 356 262 H461 Z" fill="var(--teal)"/>
    <path d="M458 150 C436 206 392 244 344 261" fill="none" stroke="var(--grey)" stroke-width="3"/>
  </svg>

  <div class="brand">
    <span class="brand__dot"></span>
    <p class="brand__name">CLEAR PATH<br>COACHING</p>
  </div>

  <div class="person">
    <h1 class="person__name">Rebecca Tanfield</h1>
    <p class="person__role">Director</p>
    <ul class="contacts">
      <li class="contacts__item">
        <svg class="contacts__icon" viewBox="0 0 12 12"><path d="M2.5 0.8 L4.3 3.2 L3.3 4.4 C4 6 5.6 7.6 7.4 8.5 L8.6 7.4 L11.1 9.2 L10 11.2 C5.5 11 0.9 6.4 0.8 2 Z" fill="var(--teal)"/></svg>
        0491 362 517
      </li>
      <li class="contacts__item">
        <svg class="contacts__icon" viewBox="0 0 12 12"><rect x="0.5" y="2.5" width="11" height="7.5" fill="var(--teal)"/><path d="M0.8 2.8 L6 7 L11.2 2.8" fill="none" stroke="#fff" stroke-width="1"/></svg>
        bec@clearpathcoaching.example.au
      </li>
      <li class="contacts__item">
        <svg class="contacts__icon" viewBox="0 0 12 12"><circle cx="6" cy="6" r="5.5" fill="var(--teal)"/><path d="M3 3.5 C4.5 3 5 4.5 4 5.5 C3.5 6.5 5 7 4.5 9 M7.5 2 C7 3.5 8.5 4 9.5 4.5 M7 7 C8 6.5 9 7.5 8.5 9" fill="none" stroke="#fff" stroke-width="0.9"/></svg>
        www.clearpathcoaching.example.au
      </li>
    </ul>
  </div>
</section>

<section class="card card--back">
  <div class="back-mark">CLEAR PATH<br>COACHING</div>
  <p class="back-url">www.clearpathcoaching.example.au</p>
</section>

</body>
</html>
```